Real Estate Webpage Design

We have an existing website: ferndaleestatecollective.com.au
We focus customised service mainly on Property Management and second-hand property sales.
We are not entirely happy about the current design and layout can stay roughly the same as the back end coding is linked to a CRM system.
We would like to see the design are more reachable to our clients and appearing.
Please check our Website Design Draft for more details.

Industry/Entity Type

Real estate Agency

Number of Pages Required

5+ page

Font styles to use
Sans Serif

Colors

Designer to choose colors to be used in the design.

```html
<!DOCTYPE html>
<html lang="en">
<head>
<meta charset="utf-8">
<title>Ferndale Estate Collective</title>
<link href="https://fonts.googleapis.com/css2?family=Quicksand:wght@500;600;700&family=Raleway:wght@400;500;600&display=swap" rel="stylesheet">
<style>
:root{
  --gold:#ebc15e;
  --gold-dark:#d9a93a;
  --navy:#2b3d53;
  --navy-deep:#23344a;
  --ink:#222;
  --muted:#666;
  --line:#ddd;
  --white:#fff;
  --black:#000;
}
*{box-sizing:border-box;margin:0;padding:0}
html,body{width:1200px;height:3063px;overflow:hidden}
body{position:relative;font-family:"Raleway",sans-serif;color:var(--ink);background:var(--white)}
.abs{position:absolute}
.head{font-family:"Quicksand",sans-serif}

/* top bar */
.topbar{left:0;top:0;width:1200px;height:79px;background:var(--white)}
.brand{display:flex;align-items:center;gap:12px}
.brand-mark{width:44px;height:44px;background:var(--gold)}
.brand-name{font-family:"Quicksand",sans-serif;font-weight:700;font-size:30px;color:var(--gold-dark);line-height:1}
.contact-chip{display:flex;align-items:center;gap:13px}
.chip-icon{width:51px;height:51px;border-radius:50%;background:var(--gold);display:flex;align-items:center;justify-content:center;flex-shrink:0}
.chip-label{font-size:14px;color:var(--ink);font-weight:500}
.chip-phone{font-family:"Quicksand",sans-serif;font-size:22px;color:var(--gold-dark);font-weight:600}
.chip-mail{font-size:14px;font-weight:500;white-space:nowrap}
.divider{width:1px;height:22px;background:var(--line)}
.lang{font-size:14px;font-weight:600}
.social-dot{width:14px;height:14px;border-radius:50%;background:var(--navy)}

/* nav */
.nav{left:0;top:79px;width:1200px;height:68px;background:var(--navy)}
.nav ul{list-style:none;display:flex;gap:39px;position:absolute;left:111px;top:24px}
.nav li{color:var(--white);font-size:16px;font-weight:500}
.login{left:907px;top:79px;width:293px;height:68px;background:var(--gold);display:flex;align-items:center;padding-left:89px;font-size:16px;font-weight:600;color:var(--navy)}

/* hero */
.hero{left:0;top:147px;width:1200px;height:600px;background:linear-gradient(180deg,#8a6a58 0%,#c4853a 25%,#7b8a5a 55%,#e6e6e2 70%,#4f6b3a 100%)}
.hero-title{left:0;width:1200px;text-align:center;color:var(--white)}
.hero-sub{top:318px;font-size:43px;font-weight:500;letter-spacing:1px}
.hero-main{top:362px;font-size:108px;font-weight:700;letter-spacing:2px}
.btn{display:flex;align-items:center;justify-content:center;border-radius:30px;font-weight:600;font-size:15px;color:var(--navy);background:var(--gold)}
.hero-btn{left:510px;top:493px;width:180px;height:56px}
.hero-arrow{top:425px}

/* about */
.about-h{left:112px;top:872px;font-size:30px;font-weight:700;color:var(--ink)}
.about-p{left:112px;top:938px;width:473px;font-size:15px;line-height:25.8px;color:#444;text-align:justify}
.about-btn{left:112px;top:1174px;width:163px;height:56px;box-shadow:0 4px 10px rgba(0,0,0,.15)}
.about-img{left:657px;top:835px;width:427px;height:416px;background:linear-gradient(135deg,#3d7ad8 0%,#c9c3bb 40%,#8b5e3c 70%,#5a4a40 100%)}

/* listings */
.listings{left:0;top:1338px;width:1200px;height:876px;background:linear-gradient(160deg,#34465c 0%,#2a3c52 60%,#25364b 100%)}
.listings-h{left:0;top:1411px;width:1200px;text-align:center;color:var(--white);font-size:29px;font-weight:700}
.tab{top:1486px;width:145px;height:56px;border:2px solid var(--gold);border-radius:30px;color:var(--gold);font-size:15px;font-weight:600;display:flex;align-items:center;justify-content:center}
.tab.active{background:var(--gold);color:var(--navy)}
.card{top:1609px;width:309px;height:466px;background:var(--white);border-radius:4px;overflow:hidden}
.card-img{width:309px;height:202px}
.pool{background:linear-gradient(180deg,#c9d9e8 0%,#e8eef3 35%,#2c58a8 60%,#1f3f86 100%)}
.tower{background:linear-gradient(180deg,#4e82cf 0%,#e9ecef 45%,#b7b9b4 75%,#5e6b4a 100%)}
.card-body{padding:16px 23px 0}
.card-title{font-family:"Quicksand",sans-serif;font-size:25px;font-weight:600;color:var(--ink)}
.card-addr{font-size:12px;color:var(--muted);margin-top:6px}
.feat{display:flex;justify-content:space-between;margin-top:24px;padding-bottom:13px;border-bottom:1px solid var(--line);font-size:13px}
.feat span{display:flex;align-items:center;gap:10px}
.insp-h{font-size:15px;font-weight:600;margin-top:16px}
.insp{display:flex;justify-content:space-between;font-size:12px;margin-top:14px;padding-bottom:12px;border-bottom:1px solid var(--line)}
.card-foot{display:flex;justify-content:space-between;align-items:center;margin-top:15px}
.card-icons{display:flex;gap:12px}
.ci{width:11px;height:11px;border-radius:2px;background:var(--navy)}
.ci.o{background:none;border:1.5px solid var(--navy)}
.price{font-family:"Quicksand",sans-serif;color:var(--gold-dark);font-size:17px;font-weight:600}

/* testimonials */
.test-h{left:0;top:2295px;width:1200px;text-align:center;font-size:29px;font-weight:700}
.test-card{left:335px;top:2364px;width:602px;height:257px;background:var(--white);box-shadow:0 4px 24px rgba(0,0,0,.1)}
.avatar{left:262px;top:2411px;width:154px;height:160px;border-radius:50%;background:linear-gradient(180deg,#c8cdd1 0%,#6e7b88 60%,#34465c 100%);border:3px solid var(--navy)}
.t-name{left:456px;top:2406px;font-size:18px;font-weight:500;letter-spacing:.5px}
.t-role{left:457px;top:2436px;font-size:15px;color:var(--navy)}
.t-text{left:457px;top:2473px;width:448px;font-size:14.5px;line-height:26px;color:#333}
.quote{left:842px;top:2395px;font-family:"Quicksand",sans-serif;font-size:90px;line-height:1;color:#f1d79b;font-weight:700}
.t-arrow{top:2469px;width:46px;height:46px;border-radius:50%;display:flex;align-items:center;justify-content:center}

/* footer */
.footer{left:0;top:2709px;width:1200px;height:354px;background:var(--black);color:var(--white)}
.f-brand .brand-name{font-size:44px}
.f-brand .brand-mark{width:56px;height:56px}
.f-social{width:41px;height:41px;border-radius:50%;background:var(--white)}
.f-h{font-family:"Quicksand",sans-serif;font-size:19px;font-weight:700}
.f-list{font-size:15px;line-height:25.6px}
.f-list b{font-weight:600}
.f-row{display:flex;gap:14px;font-size:15px;line-height:25px}
.copy{left:0;top:3025px;width:1200px;text-align:center;font-size:15px}
</style>
</head>
<body>

<header class="abs topbar">
  <div class="abs brand" style="left:111px;top:13px">
    <div class="brand-mark"></div>
    <div>
      <div class="brand-name">Ferndale</div>
      <div style="font-size:11px;color:var(--muted);margin-top:3px;letter-spacing:.5px">Estate Collective</div>
    </div>
  </div>
  <div class="abs contact-chip" style="left:408px;top:13px">
    <div class="chip-icon"><svg width="20" height="20" viewBox="0 0 24 24"><path fill="#fff" d="M6.6 10.8a15.1 15.1 0 0 0 6.6 6.6l2.2-2.2c.3-.3.7-.4 1-.2 1.1.4 2.3.6 3.6.6.6 0 1 .4 1 1V20c0 .6-.4 1-1 1A17 17 0 0 1 3 4c0-.6.4-1 1-1h3.5c.6 0 1 .4 1 1 0 1.3.2 2.5.6 3.6.1.3 0 .7-.2 1z"/></svg></div>
    <div><div class="chip-label">Call us today</div><div class="chip-phone">02 6190 4417</div></div>
  </div>
  <div class="abs divider" style="left:629px;top:28px"></div>
  <div class="abs contact-chip" style="left:651px;top:13px">
    <div class="chip-icon"><svg width="20" height="16" viewBox="0 0 20 16"><rect width="20" height="16" rx="2" fill="#fff"/><path d="M1 2l9 7 9-7" stroke="#ebc15e" stroke-width="2" fill="none"/></svg></div>
    <div class="chip-mail">info@ferndale.au</div>
  </div>
  <div class="abs divider" style="left:848px;top:28px"></div>
  <div class="abs lang" style="left:876px;top:30px">ENG &#8964;</div>
  <div class="abs divider" style="left:942px;top:28px"></div>
  <div class="abs social-dot" style="left:967px;top:32px"></div>
  <div class="abs social-dot" style="left:1000px;top:32px"></div>
  <div class="abs social-dot" style="left:1035px;top:32px"></div>
  <div class="abs social-dot" style="left:1070px;top:32px"></div>
</header>

<nav class="abs nav">
  <ul>
    <li>HOME</li><li>ABOUT US</li><li>LEASING</li><li>BUY</li><li>SELL</li><li>OUR TEAM</li><li>BLOG</li><li>CONTACT US</li>
  </ul>
</nav>
<div class="abs login">LOG IN</div>

<section class="abs hero" role="img" aria-label="White single-storey house with garden under an orange sunset sky"></section>
<div class="abs hero-title hero-sub head">WELCOME TO</div>
<div class="abs hero-title hero-main head">FERNDALE</div>
<div class="abs btn hero-btn">REQUEST QUOTE</div>
<svg class="abs hero-arrow" style="left:72px" width="24" height="42" viewBox="0 0 24 42"><path d="M20 3L4 21l16 18" stroke="#fff" stroke-width="4" fill="none"/></svg>
<svg class="abs hero-arrow" style="left:1107px" width="24" height="42" viewBox="0 0 24 42"><path d="M4 3l16 18L4 39" stroke="#fff" stroke-width="4" fill="none"/></svg>

<h2 class="abs about-h head">ABOUT US</h2>
<p class="abs about-p">Ferndale takes its name from the leafy streets we serve, buying a property is one of the most expensive expenses and important assets for people. Ferndale is a real estate company located in Gungahlin, Canberra. Being a portfolio sales agent and property manager, coupled with our high-profile international real estate experience, Ferndale is considered a market leader on the cutting edge with deep industry knowledge, ranging from landlord-tenant relationships, residential purchases.</p>
<div class="abs btn about-btn">LEARN MORE</div>
<div class="abs about-img" role="img" aria-label="Collage of homes, an interior with timber floors and a hand holding house keys"></div>

<section class="abs listings" role="img" aria-label="Dimmed photo of a person working at a laptop beside a plant"></section>
<h2 class="abs listings-h head">THIS MONTH AT FERNDALE ESTATE COLLECTIVE</h2>
<div class="abs tab active" style="left:210px">FOR SALE</div>
<div class="abs tab" style="left:369px">FOR LEASE</div>
<div class="abs tab" style="left:528px">OPEN TIMES</div>
<div class="abs tab" style="left:687px">SOLD</div>
<div class="abs tab" style="left:845px">LEASED</div>

<article class="abs card" style="left:112px">
  <div class="card-img pool" role="img" aria-label="Rooftop pool beside apartment tower"></div>
  <div class="card-body">
    <div class="card-title">Gungahlin</div>
    <div class="card-addr">Level 3/22 Banksia Row Avenue</div>
    <div class="feat"><span><svg width="24" height="14"><rect x="1" y="5" width="22" height="8" rx="2" fill="none" stroke="#555" stroke-width="1.5"/><rect x="3" y="1" width="8" height="5" fill="none" stroke="#555"/></svg>2</span><span><svg width="24" height="16"><path d="M1 7h22v3a5 5 0 0 1-5 5H6a5 5 0 0 1-5-5z" fill="none" stroke="#555" stroke-width="1.5"/></svg>2</span><span><svg width="22" height="14"><rect x="1" y="5" width="20" height="7" rx="2" fill="none" stroke="#555" stroke-width="1.5"/><path d="M4 5l3-4h8l3 4" fill="none" stroke="#555"/></svg>1</span></div>
    <div class="insp-h">Next Inspection:</div>
    <div class="insp"><span>Sat 21st May</span><span>09:40 AM - 10:00 AM</span></div>
    <div class="card-foot"><div class="card-icons"><i class="ci o" style="border-radius:50%"></i><i class="ci"></i><i class="ci"></i><i class="ci o"></i></div><div class="price">$500,000+</div></div>
  </div>
</article>
<article class="abs card" style="left:444px">
  <div class="card-img tower" role="img" aria-label="White apartment building with red balconies"></div>
  <div class="card-body">
    <div class="card-title">Belconnen</div>
    <div class="card-addr">41/9 Ironbark Lane Belconnen</div>
    <div class="feat"><span><svg width="24" height="14"><rect x="1" y="5" width="22" height="8" rx="2" fill="none" stroke="#555" stroke-width="1.5"/><rect x="3" y="1" width="8" height="5" fill="none" stroke="#555"/></svg>1</span><span><svg width="24" height="16"><path d="M1 7h22v3a5 5 0 0 1-5 5H6a5 5 0 0 1-5-5z" fill="none" stroke="#555" stroke-width="1.5"/></svg>1</span><span><svg width="22" height="14"><rect x="1" y="5" width="20" height="7" rx="2" fill="none" stroke="#555" stroke-width="1.5"/><path d="M4 5l3-4h8l3 4" fill="none" stroke="#555"/></svg>1</span></div>
    <div class="insp-h">Next Inspection:</div>
    <div class="insp"><span>Sat 21st May</span><span>09:40 AM - 10:00 AM</span></div>
    <div class="card-foot"><div class="card-icons"><i class="ci o" style="border-radius:50%"></i><i class="ci"></i><i class="ci"></i><i class="ci o"></i></div><div class="price">$500,000+</div></div>
  </div>
</article>
<article class="abs card" style="left:775px">
  <div class="card-img pool" role="img" aria-label="Rooftop pool beside apartment tower"></div>
  <div class="card-body">
    <div class="card-title">Gungahlin</div>
    <div class="card-addr">Level 3/22 Banksia Row Avenue</div>
    <div class="feat"><span><svg width="24" height="14"><rect x="1" y="5" width="22" height="8" rx="2" fill="none" stroke="#555" stroke-width="1.5"/><rect x="3" y="1" width="8" height="5" fill="none" stroke="#555"/></svg>2</span><span><svg width="24" height="16"><path d="M1 7h22v3a5 5 0 0 1-5 5H6a5 5 0 0 1-5-5z" fill="none" stroke="#555" stroke-width="1.5"/></svg>2</span><span><svg width="22" height="14"><rect x="1" y="5" width="20" height="7" rx="2" fill="none" stroke="#555" stroke-width="1.5"/><path d="M4 5l3-4h8l3 4" fill="none" stroke="#555"/></svg>1</span></div>
    <div class="insp-h">Next Inspection:</div>
    <div class="insp"><span>Sat 21st May</span><span>09:40 AM - 10:00 AM</span></div>
    <div class="card-foot"><div class="card-icons"><i class="ci o" style="border-radius:50%"></i><i class="ci"></i><i class="ci"></i><i class="ci o"></i></div><div class="price">$369,900+</div></div>
  </div>
</article>
<svg class="abs" style="left:550px;top:2118px" width="100" height="22" viewBox="0 0 100 22"><path d="M32 11H3M12 2L3 11l9 9" stroke="#8a96a5" stroke-width="3" fill="none"/><path d="M52 11h45M88 2l9 9-9 9" stroke="#ebc15e" stroke-width="3" fill="none"/></svg>

<h2 class="abs test-h head">OUR TESTIMONIALS</h2>
<div class="abs t-arrow" style="left:176px;background:#fff;box-shadow:0 2px 10px rgba(0,0,0,.12)"><svg width="20" height="14"><path d="M19 7H2M8 1L2 7l6 6" stroke="#ebc15e" stroke-width="2" fill="none"/></svg></div>
<div class="abs test-card"></div>
<div class="abs avatar" role="img" aria-label="Portrait of a smiling client"></div>
<div class="abs t-name">MIRA CALLOWAY</div>
<div class="abs t-role">Nemo enim ipsam</div>
<p class="abs t-text">Very good service. Our property manager is very responsible, Prompting and cares about detail. They use the system to track everything so no need to worry about miscommunication.I strongly rcommend this agent.</p>
<div class="abs quote">&#8221;</div>
<div class="abs t-arrow" style="left:983px;background:var(--gold)"><svg width="20" height="14"><path d="M1 7h17M12 1l6 6-6 6" stroke="#fff" stroke-width="2" fill="none"/></svg></div>

<footer class="abs footer"></footer>
<div class="abs brand f-brand" style="left:111px;top:2808px">
  <div class="brand-mark"></div>
  <div><div class="brand-name">Ferndale</div><div style="font-size:12px;color:#ddd;margin-top:3px">Estate Collective</div></div>
</div>
<div class="abs f-social" style="left:111px;top:2901px"></div>
<div class="abs f-social" style="left:168px;top:2901px"></div>
<div class="abs f-social" style="left:225px;top:2901px"></div>
<div class="abs f-social" style="left:282px;top:2901px"></div>

<div class="abs f-h" style="left:442px;top:2791px;color:#fff">Quick Links</div>
<div class="abs f-list" style="left:442px;top:2834px;color:#fff">Home<br>About Us<br>Leasing<br>Buy<br>Sell<br>More</div>

<div class="abs f-h" style="left:616px;top:2791px;color:#fff">Hours</div>
<div class="abs f-list" style="left:616px;top:2830px;color:#fff"><b>Monday to Friday</b><br>8:30 am – 5:00pm<br><b>Weekend –</b> Closed<br><b>Public holiday –</b> Closed</div>

<div class="abs f-h" style="left:844px;top:2791px;color:#fff">Contact Us</div>
<div class="abs f-row" style="left:844px;top:2837px;color:#fff"><svg width="13" height="18" viewBox="0 0 13 18" style="margin-top:4px"><path d="M6.5 0A6.5 6.5 0 0 0 0 6.5C0 11 6.5 18 6.5 18S13 11 13 6.5A6.5 6.5 0 0 0 6.5 0z" fill="#fff"/><circle cx="6.5" cy="6.5" r="2.3" fill="#000"/></svg><span>18/7 Wattle Crest Ave,<br>Harwood, ACT, 2913</span></div>
<div class="abs f-row" style="left:844px;top:2905px;color:#fff"><svg width="16" height="16" viewBox="0 0 24 24" style="margin-top:4px"><path fill="#fff" d="M6.6 10.8a15.1 15.1 0 0 0 6.6 6.6l2.2-2.2c.3-.3.7-.4 1-.2 1.1.4 2.3.6 3.6.6.6 0 1 .4 1 1V20c0 .6-.4 1-1 1A17 17 0 0 1 3 4c0-.6.4-1 1-1h3.5c.6 0 1 .4 1 1 0 1.3.2 2.5.6 3.6.1.3 0 .7-.2 1z"/></svg><span>02 6190 4417</span></div>
<div class="abs f-row" style="left:844px;top:2945px;color:#fff"><svg width="15" height="12" viewBox="0 0 20 16" style="margin-top:7px"><rect width="20" height="16" rx="2" fill="#fff"/><path d="M1 2l9 7 9-7" stroke="#000" stroke-width="2" fill="none"/></svg><span style="font-size:14px">info@ferndale.au</span></div>

<div class="abs copy" style="color:#fff">©Copyrights 2022 Ferndale &nbsp;| &nbsp; All Rights Reserved</div>

</body>
</html>
```